Website for popular Orbix App

We need a website for our popular Orbix App "KORVO - Pocket Coder". KORVO is an App to make Apps:

https://apps.vendexa.example/listing?id=net.korvo.app

We need the homepage design as well as the design for additional content pages. If possible post both designs when submitting.

On the homepage we would like to see the following elements:

- slogan + short description (exact wording tbd)

- logo (attached)

- embedded youtube video http://clipvu.example/Tq8mPw3Lk2d and/or image showing mobile devices with app screenshots (attached)

- link to Vendexa Apps: https://apps.vendexa.example/listing?id=net.korvo.app

- link to Circlora (should be highly visible): https://circlora.example/558102947361029485712/feed

- less visible links to Chirpla & Friendvo

- statement: ">1000000 downloads"

- press coverage:

Gizmoreel - http://www.gizmoreel.example/2012/03/07/build-apps-with-korvo-clip/
Handset Herald - http://www.handsetherald.example/2012/03/06/phones-get-a-pocket-coder-that-lets-you-write-apps-right-on-your-tablet-which-now-wants-a-mirror-joke/
The Ledgerline - http://www.ledgerline.example/2012/03/13/mobile_kit/
TechBriq - http://www.techbriq.example/news/2012/03/KORVO/
Bytespur - http://coders.bytespur.example/story/12/03/14/8826401/trial-release-of-korvo-allows-app-building-on-phones

- user testimonials (taken from some 5 star Vendexa Apps ratings)

- links to the content pages, e.g. "About us", "Features", "Getting started", "Community"

- anything else that comes to your mind

```html
<!DOCTYPE html>
<html lang="en">
<head>
<meta charset="utf-8">
<title>KORVO - Pocket Coder</title>
<link href="https://fonts.googleapis.com/css2?family=Open+Sans:ital,wght@0,300;0,400;0,600;1,300&family=Ubuntu:wght@300;400;500;700&display=swap" rel="stylesheet">
<style>
:root{
  --teal:#1f9fd6;
  --teal-dark:#1588c0;
  --green:#7ab51d;
  --green-light:#8fcb22;
  --green-dark:#5f9412;
  --text:#333;
  --muted:#777;
  --line:#e4e4e4;
  --panel:#f2f2f2;
  --star:#f39c12;
  --star-off:#cfcfcf;
  --badge:#4a4a4a;
}
*{margin:0;padding:0;box-sizing:border-box}
html,body{width:853px;height:1200px;overflow:hidden;background:#fff}
body{position:relative;font-family:"Open Sans",sans-serif;color:var(--text)}
.abs{position:absolute}
h1,h2,h3,.nav a,.brand,.btn,.footer-nav{font-family:"Ubuntu",sans-serif}

/* header */
.brand-mark{left:53px;top:16px;width:62px;height:62px;border:3px solid var(--teal);border-radius:6px}
.brand{left:138px;top:20px;font-size:36px;font-weight:500;color:var(--teal);line-height:1}
.brand-tag{left:136px;top:61px;font-size:15px;color:var(--teal);font-family:"Ubuntu",sans-serif;font-weight:400}
.social{top:22px;width:22px;height:22px;border-radius:4px;background:var(--teal)}
.search{left:615px;top:53px;width:186px;height:25px;border:1px solid #ddd;font-size:10px;font-style:italic;color:#999;padding:6px 9px}
.search svg{position:absolute;right:8px;top:5px}

/* nav */
.nav{left:0;top:88px;width:853px;height:42px;background:linear-gradient(var(--green-light),var(--green));border-bottom:2px solid var(--green-dark);display:flex;padding-left:51px}
.nav a{color:#fff;text-decoration:none;font-size:14px;font-weight:500;padding:0 15px;line-height:42px;border-right:1px solid rgba(255,255,255,.35)}
.nav a:last-child{border-right:0}

/* hero */
.hero{left:0;top:130px;width:853px;height:296px;background:linear-gradient(#fff 40%,#ececec)}
.hero-kicker{left:63px;top:173px;font-size:22px;font-weight:300;color:var(--teal)}
.hero-title{left:63px;top:201px;font-size:27px;font-weight:700;color:var(--teal)}
.hero-sub{left:63px;top:236px;font-size:14px;font-weight:400;color:#222}
.hero-copy{left:62px;top:259px;width:290px;font-size:9.5px;line-height:14.5px;color:var(--muted)}
.btn{left:61px;top:312px;width:91px;height:25px;background:linear-gradient(#2fb3ea,var(--teal-dark));color:#fff;font-size:10px;font-weight:500;text-align:center;line-height:25px;border-radius:2px}
.dots{left:63px;top:355px;display:flex;gap:3px}
.dots span{width:8px;height:8px;border-radius:50%;background:#ccc}
.dots span:first-child{background:#111}
.video{left:436px;top:155px;width:332px;height:227px;background:#fff;border:1px solid #ddd;padding:5px}
.video-inner{width:100%;height:100%;background:#333;position:relative}
.video-screen{position:absolute;left:107px;top:15px;width:106px;height:198px;background:linear-gradient(#f6f6f6 55%,#3a3a3a 55%)}
.video-play{position:absolute;left:140px;top:89px}
.video-shadow{left:445px;top:384px;width:310px;height:14px;background:radial-gradient(ellipse at center,rgba(0,0,0,.18),transparent 70%)}

/* welcome */
.welcome-title{left:49px;top:461px;font-size:17px;font-weight:400;color:#333}
.welcome-copy{left:50px;top:490px;width:530px;font-size:9.4px;line-height:16.4px;color:#555;font-weight:300;letter-spacing:-0.1px}
.welcome-copy p+p{margin-top:16px}

/* press */
.press-title{left:49px;top:648px;font-size:17px;font-weight:400}
.press{left:47px;top:677px;width:534px;height:400px;border:1px solid var(--line);box-shadow:0 1px 3px rgba(0,0,0,.06)}
.press-row{position:absolute;left:8px;width:516px;border-bottom:1px solid var(--line)}
.press-logo{position:absolute;left:14px;width:150px;display:flex;align-items:center;justify-content:center;gap:7px;font-family:"Open Sans",sans-serif;font-weight:600;font-size:16px;color:var(--badge)}
.press-logo i{width:12px;height:12px;background:var(--badge);display:block;flex:none}
.press-name{position:absolute;left:177px;font-family:"Ubuntu",sans-serif;font-size:12px;color:#333}
.press-text{position:absolute;left:177px;width:320px;font-size:9.6px;line-height:15px;color:#888}

/* sidebar */
.store{left:600px;top:454px;width:205px;height:63px;background:#000;border:1px solid #444;color:#fff;font-family:"Open Sans",sans-serif;font-size:19px;display:flex;align-items:center;gap:10px;padding-left:26px}
.store i{width:22px;height:22px;background:#fff;display:block}
.downloads{left:600px;top:525px;width:205px;height:42px;background:linear-gradient(#35b9ee,var(--teal-dark));color:#fff;font-family:"Ubuntu",sans-serif;font-size:17px;text-align:center;line-height:42px;border-radius:2px}
.shots-title{left:600px;top:594px;font-size:15px;font-weight:400;color:var(--green)}
.shot{left:600px;top:618px;width:205px;height:131px;background:linear-gradient(#1a1d22,#0b0c0f 80%,#223344);border:2px solid #111}
.testi{left:600px;top:752px;width:205px;height:324px;border:1px solid var(--line)}
.testi-head{height:34px;background:var(--panel);border-bottom:1px solid var(--line);font-family:"Ubuntu",sans-serif;font-size:15.5px;padding:7px 21px;position:relative}
.testi-head svg{position:absolute;left:114px;top:10px}
.quote{position:absolute;left:20px;width:172px;font-size:9px;font-style:italic;font-weight:300;line-height:16.4px;color:#555}
.author{position:absolute;left:20px;font-size:9px;font-weight:600;color:#333}
.author b{font-size:13px;letter-spacing:1px;color:var(--star);font-weight:400;margin-left:3px}
.author b em{color:var(--star-off);font-style:normal}

/* footer */
.footer{left:0;top:1106px;width:853px;height:94px;background:linear-gradient(#f0f0f0,#fff 40%)}
.footer-nav{left:46px;top:1131px;font-size:11px;color:#333}
.footer-nav span{color:#555;margin:0 4px}
.copy{left:47px;top:1156px;font-size:8px;color:#555}
</style>
</head>
<body>

<!-- header -->
<div class="abs brand-mark" aria-hidden="true"></div>
<div class="abs brand">KORVO</div>
<div class="abs brand-tag">Korlang IDE for Orbix</div>
<div class="abs social" style="left:725px" role="img" aria-label="Chirpla"></div>
<div class="abs social" style="left:752px" role="img" aria-label="Friendvo"></div>
<div class="abs social" style="left:779px" role="img" aria-label="Circlora"></div>
<div class="abs search">Search here..
  <svg width="14" height="14" viewBox="0 0 14 14"><circle cx="6" cy="6" r="4.5" fill="none" stroke="#888" stroke-width="2"/><line x1="9.3" y1="9.3" x2="13" y2="13" stroke="#888" stroke-width="2.2"/></svg>
</div>

<nav class="abs nav">
  <a>Home</a><a>About Us</a><a>Our Application</a><a>How it Works</a><a>Videos</a><a>Testimonials</a><a>Press News</a><a>Contact</a>
</nav>

<!-- hero -->
<div class="abs hero"></div>
<h2 class="abs hero-kicker">Mauris vel lacus vitae</h2>
<h1 class="abs hero-title">Nunc tempus felis vitae</h1>
<h3 class="abs hero-sub">Duis tincidunt lectus quis dui viverra</h3>
<p class="abs hero-copy">Mauris vel lacus vitae felis vestibulum volutpat. Etiam est nunc, venenatis in, tristique eu, imperdiet ac, nisl. Cum sociis natoque penatibus et magnis dis parturient montes</p>
<div class="abs btn">GET STARTED</div>
<div class="abs dots"><span></span><span></span><span></span><span></span></div>

<div class="abs video-shadow"></div>
<div class="abs video">
  <div class="video-inner">
    <div class="video-screen" role="img" aria-label="App screen with code editor and on-screen keyboard"></div>
    <svg class="video-play" width="36" height="36" viewBox="0 0 36 36"><circle cx="18" cy="18" r="18" fill="#1a1a1a"/><polygon points="14,10 14,26 27,18" fill="#fff"/></svg>
  </div>
</div>

<!-- welcome -->
<h2 class="abs welcome-title">Welcome to Our Website Mainpage..</h2>
<div class="abs welcome-copy">
  <p>KORVO is an integrated development environment (IDE) for developing real Orbix Apps directly on Orbix devices. KORVO supports the full edit-compile-run cycle: write code with the feature rich editor offering advanced features like code completion, real-time error checking, refactoring and smart code navigation, and run your App with a single click.</p>
  <p>KORVO will turn your Orbix tablet with keyboard into a real development box. We use the Slatebook Pro running Maple Swirl to code with KORVO. KORVO will turn your Orbix Phone into a small development computer to browse and touch your code on the go</p>
</div>

<!-- press -->
<h2 class="abs press-title">Press Coverage</h2>
<div class="abs press">
  <div class="press-row" style="top:0;height:75px">
    <div class="press-logo" style="top:29px"><i></i>Gizmoreel</div>
    <div class="press-name" style="top:13px;left:181px">Gizmoreel</div>
    <div class="press-text" style="top:33px;left:181px">Duis tincidunt lectus quis dui viverra vestibulum. Suspendisse vulputate aliquam dui. Nulla elementum dui ut augue.</div>
  </div>
  <div class="press-row" style="top:75px;height:74px">
    <div class="press-logo" style="top:27px"><i></i>Handset Herald</div>
    <div class="press-name" style="top:10px;left:179px">Handset Herald</div>
    <div class="press-text" style="top:28px;left:179px">Duis tincidunt lectus quis dui viverra vestibulum. Suspendisse vulputate aliquam dui. Nulla elementum dui ut augue.</div>
  </div>
  <div class="press-row" style="top:149px;height:79px">
    <div class="press-logo" style="top:28px"><i></i>The Ledgerline</div>
    <div class="press-name" style="top:11px">The Ledgerline</div>
    <div class="press-text" style="top:29px">Duis tincidunt lectus quis dui viverra vestibulum. Suspendisse vulputate aliquam dui. Nulla elementum dui ut augue.</div>
  </div>
  <div class="press-row" style="top:228px;height:79px">
    <div class="press-logo" style="top:28px"><i></i>TechBriq</div>
    <div class="press-name" style="top:10px">TechBriq</div>
    <div class="press-text" style="top:28px">Duis tincidunt lectus quis dui viverra vestibulum. Suspendisse vulputate aliquam dui. Nulla elementum dui ut augue.</div>
  </div>
  <div class="press-row" style="top:307px;height:90px;border-bottom:0">
    <div class="press-logo" style="top:27px"><i></i>Bytespur</div>
    <div class="press-name" style="top:13px">Bytespur</div>
    <div class="press-text" style="top:31px">Duis tincidunt lectus quis dui viverra vestibulum. Suspendisse vulputate aliquam dui. Nulla elementum dui ut augue.</div>
  </div>
</div>

<!-- sidebar -->
<div class="abs store"><i aria-hidden="true"></i>Vendexa Apps</div>
<div class="abs downloads">1000000 downloads</div>
<h2 class="abs shots-title">Apps Screenshots</h2>
<div class="abs shot" role="img" aria-label="Screenshot of the code editor in the app"></div>

<div class="abs testi">
  <div class="testi-head">Testimonials
    <svg width="22" height="14" viewBox="0 0 22 14"><ellipse cx="11" cy="6.5" rx="11" ry="6.5" fill="#dcdcdc"/></svg>
  </div>
  <p class="quote" style="top:46px">Nunc tempus felis vitae urna. Vivamus porttitor, g, purus nisi eleifend libero, a tempus libero lectus feugiat felis. Morbi diam mauris, viverra in, gravida eu</p>
  <div class="author" style="top:117px">By Author Name <b>★★★★</b></div>
  <p class="quote" style="top:146px;left:18px">Nunc tempus felis vitae urna. Vivamus port-titor, g, purus nisi eleifend libero, a tempus libero lectus feugiat felis.</p>
  <div class="author" style="top:201px;left:18px">By Author Name <b>★★★<em>★</em></b></div>
  <p class="quote" style="top:230px">Mauris vel lacus vitae felis vestibulum volut-pat. Etiam est nunc, venenatis in, tristique eu, imperdiet ac, nisl. Cum sociis</p>
  <div class="author" style="top:285px">By Author Name <b>★★<em>★</em></b></div>
</div>

<!-- footer -->
<div class="abs footer"></div>
<div class="abs footer-nav">Home<span>|</span>About Us<span>|</span>Our Application<span>|</span>How it Works<span>|</span>Videos<span>|</span>Testimonials<span>|</span>Press News<span>|</span>Contact</div>
<div class="abs copy">Copyright © 2013 Company Name. &nbsp;All right reserved. &nbsp;Term of Use</div>

</body>
</html>
```